Flyer Design for Wedding Showcase

We are a modern Australian Restaurant situated on the Swan River in Perth boasting beautiful city views. We require a DL size flyer one sided to promote our wedding open evening which we hold every year.

Heading: Corella Point Restaurant Wedding Showcase
19th September 2014 from 5pm to 8pm
Address: Corella Point Restaurant, 17 Brindle Parade, Wexton WA 6112
Contact for more information: 08 9561 7284

There is several suppliers showcasing every year and we also have cocktail food and wine tastings at the event. Clients will also have the opportunity to chat to the function coordinators from Corella Point Restaurant.

We would like a modern, elegant design with a warm feeling to it. Couples getting married should be able to relate and identify with this design.

Target Market(s)

Young couples looking to get married

Industry/Entity Type

Wedding

Colors
3276b5
cee9f5
85abd2
eea4c8

Requirements
Must have
• Must have the following blurb:
Corella Point Restaurant is Perth's premium wedding venue situated on the Swan River boasting beautiful views of the Perth city skyline.
Come and meet our team and some of our favorite wedding suppliers while enjoying this beautiful location and sampling some of the food and wine we offer.

Logo needs to be on flyer
Should not have
• hot pink

```html
<!DOCTYPE html>
<html lang="en">
<head>
<meta charset="utf-8">
<title>Wedding Showcase – Corella Point Restaurant</title>
<link rel="stylesheet" href="https://fonts.googleapis.com/css2?family=Great+Vibes&family=Tinos&display=swap">
<style>
  :root {
    --ink: #231f20;
    --brand-blue: #3276b5;
    --sky-pale: #cee9f5;
    --sky-mid: #85abd2;
    --blush: #eea4c8;
    --paper: #f4f3f1;
    --paper-light: #fbfbfa;
    --rule: #c9c6c2;
  }
  * { margin: 0; padding: 0; box-sizing: border-box; }
  html, body { width: 1200px; height: 2544px; overflow: hidden; }
  body { background: var(--paper); }
  .flyer {
    position: relative;
    width: 1200px;
    height: 2544px;
    overflow: hidden;
    background: linear-gradient(115deg, var(--paper-light) 0%, var(--paper) 45%, var(--paper-light) 70%, #ecebe8 100%);
    color: var(--ink);
  }
  .hero-photo {
    position: absolute;
    left: 0; top: 0;
    width: 1200px; height: 1278px;
    background:
      linear-gradient(180deg,
        #9fc0dc 0%, #cfdbe6 24%, #e9d6d8 38%, #b9c3cf 46%,
        #8f9ea8 50%, #6f8f3e 56%, #5f8a2c 75%, #4f7a24 100%);
  }
  .event-date {
    position: absolute;
    top: 1318px; left: 0; width: 100%;
    text-align: center;
    font-family: "Tinos", "Times New Roman", serif;
    font-size: 44px;
    letter-spacing: 1px;
  }
  .event-time {
    position: absolute;
    top: 1378px; left: 0; width: 100%;
    text-align: center;
    font-family: "Tinos", "Times New Roman", serif;
    font-size: 30px;
  }
  .headline {
    position: absolute;
    left: 0; top: 1470px; width: 100%;
    font-family: "Great Vibes", cursive;
    font-weight: 400;
    color: var(--ink);
    line-height: 1;
  }
  .headline-line {
    display: block;
    font-size: 236px;
  }
  .headline-line.first { margin-left: 104px; }
  .headline-line.second { margin-left: 372px; margin-top: -12px; }
  .blurb {
    position: absolute;
    top: 1986px; left: 60px; width: 1080px;
    text-align: center;
    font-family: "Tinos", "Times New Roman", serif;
    font-size: 35px;
    line-height: 43px;
  }
  .divider {
    position: absolute;
    left: 50px; width: 1100px; height: 2px;
    background: var(--rule);
  }
  .divider.top { top: 1962px; }
  .divider.bottom { top: 2232px; }
  .brand {
    position: absolute;
    left: 116px; top: 2336px;
    display: flex; align-items: center; gap: 14px;
  }
  .brand-dot {
    width: 34px; height: 34px; border-radius: 50%;
    background: var(--brand-blue);
  }
  .brand-name {
    font-family: "Tinos", "Times New Roman", serif;
    font-size: 30px;
    letter-spacing: 3px;
    color: var(--brand-blue);
    white-space: nowrap;
  }
  .contact {
    position: absolute;
    left: 526px; top: 2270px;
    font-family: "Tinos", "Times New Roman", serif;
    font-size: 33px;
    line-height: 37px;
  }
  .contact-label { color: var(--brand-blue); }
  .contact-value { color: var(--ink); }
  .contact-label.second { margin-top: 10px; }
</style>
</head>
<body>
  <main class="flyer">
    <div class="hero-photo" role="img" aria-label="Outdoor wedding ceremony setup on a riverside lawn: rows of wooden chairs with flower jars along an aisle leading to a leafy arch, a marina and city skyline at dusk behind, framed by overhanging trees"></div>

    <p class="event-date">19th September 2014</p>
    <p class="event-time">from 5pm to 8pm</p>

    <h1 class="headline">
      <span class="headline-line first">Wedding</span>
      <span class="headline-line second">Showcase</span>
    </h1>

    <div class="divider top"></div>
    <p class="blurb">Corella Point Restaurant is Perth's premium wedding venue<br>situated on the Swan River boasting beautiful views of the Perth<br>city skyline. Come and meet our team and some of our favorite<br>wedding suppliers while enjoying this beautiful location and<br>sampling some of the food and wine we offer.</p>
    <div class="divider bottom"></div>

    <div class="brand">
      <span class="brand-dot"></span>
      <span class="brand-name">CORELLA POINT</span>
    </div>

    <div class="contact">
      <p class="contact-label">Address:</p>
      <p class="contact-value">Corella Point Restaurant, 17<br>Brindle Parade, Wexton WA 6112</p>
      <p class="contact-label second">Contact for more information:</p>
      <p class="contact-value">08 9561 7284</p>
    </div>
  </main>
</body>
</html>
```